Melorix artwork for new single release

I need Melorix artwork creating to release a new single on there.

The specs are:

Ideal size: 3000 x 3000 pixels
Minimum size: 1400 x 1400 pixels
Aspect ratio: 1:1 (must be a perfect square)
File format: JPG or PNG
Color space: sRGB
File size: Max 4MB

The song is called "Was It Ever Rain?"
The artist is "Martin Hollow"

We have no images of Martin, so it really is open to imagination.

Target Market(s)

Melorix listeners

Industry/Entity Type

Music

```html
<!DOCTYPE html>
<html lang="en">
<head>
<meta charset="utf-8">
<title>Was It Ever Rain? — Martin Hollow</title>
<link rel="stylesheet" href="https://fonts.googleapis.com/css2?family=Mr+Dafoe&family=Montserrat:wght@500&display=swap">
<style>
  :root {
    --pane-green-light: #b9b27a;
    --pane-green: #5f7a3c;
    --pane-green-deep: #3e5a2a;
    --pane-blue-light: #a39a8f;
    --pane-blue: #4f5c6c;
    --pane-blue-deep: #2d3a4a;
    --pane-amber-light: #c7a55a;
    --pane-amber: #6b5a3e;
    --pane-amber-deep: #3b3024;
    --pane-rose-light: #c9a393;
    --pane-rose: #8e7469;
    --pane-rose-deep: #4a4038;
    --frame: #231915;
    --frame-edge: #3b2b23;
    --title-ink: #fbf6ec;
    --artist-ink: #cdb7ae;
  }
  * { margin: 0; padding: 0; box-sizing: border-box; }
  html, body {
    width: 1200px; height: 1200px; overflow: hidden;
    background: var(--frame);
  }
  .cover {
    position: relative;
    width: 1200px; height: 1200px;
    overflow: hidden;
    background: var(--frame);
  }
  .pane { position: absolute; }
  .pane--top-left {
    left: 0; top: 0; width: 612px; height: 594px;
    background:
      radial-gradient(ellipse 260px 300px at 470px 170px, rgba(240,205,150,.75), transparent 70%),
      radial-gradient(ellipse 420px 380px at 200px 240px, var(--pane-green-light), transparent 75%),
      linear-gradient(160deg, var(--pane-green) 0%, var(--pane-green-deep) 100%);
  }
  .pane--top-right {
    left: 665px; top: 0; width: 535px; height: 585px;
    background:
      radial-gradient(ellipse 240px 320px at 170px 280px, rgba(205,160,120,.6), transparent 70%),
      radial-gradient(ellipse 300px 380px at 120px 120px, var(--pane-blue-light), transparent 75%),
      linear-gradient(200deg, var(--pane-blue) 0%, var(--pane-blue-deep) 100%);
  }
  .pane--bottom-left {
    left: 0; top: 652px; width: 606px; height: 548px;
    background:
      radial-gradient(ellipse 200px 260px at 40px 260px, rgba(230,200,110,.9), transparent 70%),
      radial-gradient(ellipse 200px 400px at 400px 220px, rgba(200,175,150,.45), transparent 70%),
      linear-gradient(180deg, var(--pane-amber) 0%, var(--pane-amber-light) 55%, var(--pane-amber-deep) 100%);
  }
  .pane--bottom-right {
    left: 665px; top: 645px; width: 535px; height: 555px;
    background:
      radial-gradient(ellipse 260px 260px at 340px 160px, rgba(220,170,160,.8), transparent 70%),
      radial-gradient(ellipse 400px 300px at 120px 420px, rgba(190,160,120,.6), transparent 75%),
      linear-gradient(170deg, var(--pane-rose-light) 0%, var(--pane-rose) 60%, var(--pane-rose-deep) 100%);
  }
  .window-frame {
    position: absolute; inset: 0;
    width: 1200px; height: 1200px;
  }
  .title {
    position: absolute;
    left: 110px; top: 960px;
    font-family: "Mr Dafoe", cursive;
    font-weight: 400;
    font-size: 136px;
    line-height: 1;
    color: var(--title-ink);
    transform: rotate(-13deg);
    transform-origin: left center;
    white-space: nowrap;
    text-shadow: 0 2px 8px rgba(0,0,0,.25);
  }
  .artist {
    position: absolute;
    left: 0; right: 0; top: 1080px;
    text-align: center;
    padding-left: 64px;
    font-family: "Montserrat", sans-serif;
    font-weight: 500;
    font-size: 44px;
    line-height: 1;
    letter-spacing: 0.28em;
    color: var(--artist-ink);
    opacity: .85;
  }
</style>
</head>
<body>
  <main class="cover">
    <div class="pane pane--top-left" role="img" aria-label="Photo through a fogged pane: a woman's profile, lit warmly, beside a heart traced in the condensation"></div>
    <div class="pane pane--top-right" role="img" aria-label="Photo through a fogged pane: the back of her long hair in soft blue shadow"></div>
    <div class="pane pane--bottom-left" role="img" aria-label="Photo through a fogged pane: her shoulder and a warm lamp glow"></div>
    <div class="pane pane--bottom-right" role="img" aria-label="Photo through a fogged pane: dusky pink condensation with a question mark traced in it"></div>

    <svg class="window-frame" viewBox="0 0 1200 1200" aria-hidden="true">
      <polygon points="612,0 665,0 662,1200 606,1200" fill="var(--frame)"/>
      <polygon points="0,594 1200,585 1200,645 0,652" fill="var(--frame)"/>
      <line x1="612" y1="0" x2="606" y2="1200" stroke="var(--frame-edge)" stroke-width="3"/>
      <line x1="0" y1="652" x2="1200" y2="645" stroke="var(--frame-edge)" stroke-width="3"/>
    </svg>

    <h1 class="title">Was It Ever Rain?</h1>
    <p class="artist">MARTIN HOLLOW</p>
  </main>
</body>
</html>
```